Flyer-Design für Musikverein - Jugendkapelle
Zielgruppe
Musikverein Musterdorf
Unsere Zielgruppe sind Kinder und Jugendliche, die ein Instrument erlernen wollen.
Der Einstieg der jüngsten geht in einem Alter ab ca. 8 Jahren los. Die meisten neuen Musiker steigen zwischen 10 - 14 Jahren ein.
Der Flyer soll aber auch geeignet sein um an Grund- und weiterführenden Schulen ausgelegt werden zu können um Musiker für die Jugendkapelle zu gewinnen. Dementsprechend frisch und interessant soll der Flyer gestaltet sein.
Aufgabenstellung
Es soll ansprechend sein für Jugendliche, frisch, fröhlich und soll das Interesse der jugendlichen mit dem Design wecken.
Es soll die Jugendlichkeit, die Blasmusik und das Vereinsleben miteinander verbinden, sowie die Vorteile und der Spaß an der Musik (Instrument erlernen, Spaß am Musizieren, neue Freunde und Kameradschaft und auch Freizeitaktivitäten) miteinander darstellen.

```html
<!DOCTYPE html>
<html lang="de">
<head>
<meta charset="utf-8">
<title>Musik macht Freu(n)de – Jugendkapelle</title>
<link rel="stylesheet" href="https://fonts.googleapis.com/css2?family=Caveat+Brush&family=Work+Sans:wght@400;500;700;800&display=swap">
<style>
  :root {
    --bg: #f9c557;
    --blob: #f08a3a;
    --blob-light: #f3a04f;
    --accent: #e8692a;
    --highlight: #ffdd55;
    --white: #ffffff;
    --ink: #1a1a1a;
  }
  * { margin: 0; padding: 0; box-sizing: border-box; }
  html, body { width: 851px; height: 1200px; overflow: hidden; background: var(--bg); }
  .flyer {
    position: relative;
    width: 851px;
    height: 1200px;
    background: var(--bg);
    font-family: "Work Sans", sans-serif;
    color: var(--white);
    overflow: hidden;
  }
  .brush-blob { position: absolute; left: 0; top: 0; width: 640px; height: 520px; }
  .hand { font-family: "Caveat Brush", cursive; font-weight: 400; }
  .headline {
    position: absolute; left: 82px; top: 70px;
    font-size: 104px; line-height: 1; letter-spacing: 2px; color: var(--white); white-space: nowrap;
  }
  .notes {
    position: absolute; left: 672px; top: 66px; width: 130px; height: 80px;
    font-size: 44px; color: var(--ink); line-height: 1;
  }
  .notes span { position: absolute; }
  .tagline {
    position: absolute; left: 84px; top: 193px;
    font-weight: 700; font-size: 26px; white-space: nowrap;
  }
  .highlight-band { position: absolute; background: var(--highlight); }
  .band-friends { left: 440px; top: 172px; width: 340px; height: 68px; transform: rotate(-4deg); }
  .friends {
    position: absolute; left: 453px; top: 150px;
    font-size: 81px; line-height: 1; transform: rotate(-4deg); letter-spacing: 2px; white-space: nowrap;
  }
  .intro { position: absolute; left: 79px; top: 324px; font-size: 30px; line-height: 38px; letter-spacing: 0.5px; white-space: nowrap; }
  .intro strong, .offer strong { font-weight: 700; }
  .offer { position: absolute; left: 79px; top: 431px; font-size: 24.5px; line-height: 29.5px; letter-spacing: 0.6px; white-space: nowrap; }
  .section-title {
    position: absolute; left: 79px; top: 526px;
    font-size: 30.5px; font-weight: 700; color: var(--accent); letter-spacing: 0.5px;
  }
  .benefits { position: absolute; left: 91px; top: 598px; list-style: none; font-size: 24.4px; line-height: 34.5px; letter-spacing: 0.8px; white-space: nowrap; }
  .benefits li { position: relative; padding-left: 32px; }
  .benefits li::before {
    content: ""; position: absolute; left: 0; top: 12px;
    width: 14px; height: 12px; background: var(--accent); border-radius: 3px;
  }
  .instruments-title {
    position: absolute; left: 82px; top: 798px;
    font-size: 58px; line-height: 1; letter-spacing: 1px; white-space: nowrap;
  }
  .band-learn { left: 392px; top: 836px; width: 390px; height: 46px; transform: rotate(-3deg); }
  .learn {
    position: absolute; left: 406px; top: 836px;
    font-weight: 700; font-size: 30px; transform: rotate(-3deg); letter-spacing: 0.5px; white-space: nowrap;
  }
  .instrument-list {
    position: absolute; list-style: none; white-space: nowrap;
    color: var(--accent); font-weight: 700; font-size: 27.5px; line-height: 40.3px; letter-spacing: 0.5px;
  }
  .col-brass { left: 106px; top: 940px; }
  .col-mixed { left: 471px; top: 942px; }
  .icon-slot { position: absolute; background: rgba(255,255,255,0.3); border-radius: 14px; }
  .icon-trumpet { left: 194px; top: 922px; width: 70px; height: 108px; transform: rotate(-30deg); }
  .icon-drum { left: 630px; top: 1036px; width: 78px; height: 70px; border-radius: 38px 38px 12px 12px; }
</style>
</head>
<body>
<main class="flyer">
  <svg class="brush-blob" viewBox="0 0 640 520" role="img" aria-label="Orangefarbener Aquarell-Pinselstrich als Hintergrundfläche">
    <defs>
      <radialGradient id="blobTone" cx="40%" cy="40%" r="70%">
        <stop offset="0" stop-color="#f2913f"/>
        <stop offset="1" stop-color="#ef8434"/>
      </radialGradient>
    </defs>
    <path fill="url(#blobTone)" d="M0 48 C160 70 380 95 480 117 C530 130 565 148 583 172 C605 200 620 220 618 240 C616 280 612 315 604 343 C580 410 530 460 480 480 C430 495 380 496 343 494 C290 490 250 484 206 480 C150 474 110 468 69 466 L0 466 Z"/>
    <path fill="#f3a04f" opacity="0.6" d="M300 140 C380 128 470 150 540 195 C585 230 590 290 560 330 C520 360 440 350 380 320 C330 290 305 240 296 200 C292 175 292 150 300 140 Z"/>
  </svg>

  <h1 class="headline hand">MUSIK MACHT</h1>
  <div class="notes" aria-hidden="true">
    <span style="left:0;top:30px">♪</span>
    <span style="left:46px;top:0">♫</span>
    <span style="left:96px;top:24px">♪</span>
  </div>
  <p class="tagline">Wer will Musiker werden?</p>
  <div class="highlight-band band-friends"></div>
  <p class="friends hand">FREU(N)DE</p>

  <p class="intro">Probiere es bei uns aus, beim <strong>MV MUSTERDORF</strong><br><strong>Hast du Lust, bei uns mitzumachen?</strong></p>
  <p class="offer">Wir bieten im Bereich Blasmusik qualifizierten Musik-<br>unterricht für <strong>Kinder und Jugendliche</strong> an.</p>

  <h2 class="section-title">Unsere Leistungen:</h2>
  <ul class="benefits">
    <li>Einzelunterricht</li>
    <li>Lehrkräfte mit Musikausbildung und<br>langjähriger pädagogischer Erfahrung</li>
    <li>Unterrichtsbeginn immer am Monatsbeginn</li>
  </ul>

  <h2 class="instruments-title hand">Folgende Instrumente</h2>
  <div class="highlight-band band-learn"></div>
  <p class="learn">können erlernt werden:</p>

  <div class="icon-slot icon-trumpet" role="img" aria-label="Weiße Strichzeichnung einer Trompete"></div>
  <ul class="instrument-list col-brass">
    <li>Trompete / Flügelhorn</li>
    <li>Tuba</li>
    <li>Tenorhorn / Bariton</li>
    <li>/ Posaune</li>
  </ul>
  <ul class="instrument-list col-mixed">
    <li>Waldhorn</li>
    <li>Klarinette, Saxophon</li>
    <li>Querflöte</li>
    <li>Schlagzeug</li>
  </ul>
  <div class="icon-slot icon-drum" role="img" aria-label="Weiße Strichzeichnung einer Trommel"></div>
</main>
</body>
</html>
```